Need step-by-step retouch guide to make photo looks like 'included example'

Hi all creative designer,

I just browse the web and really like this style of retouch.
The color tone is so cute and skin is smooth.

http://node4.cdn.pixvane.net/3921/7730194562_b81d04fa27_m.jpg
http://node4.cdn.pixvane.net/3928/7746302981_c9a713e0d4_m.jpg
^ I like these photo's color tone
http://node4.cdn.pixvane.net/4410/7761928340_f02b85d7a1_m.jpg
http://node2.cdn.pixvane.net/1873/7702483916_ad54c9e103_m.jpg
http://node4.cdn.pixvane.net/3967/7219845063_e3b08f6c52_m.jpg
^ I like these skin retouch.

And here is the important part.
I need someone to teach me how to do that. Skin retouch and color tone like the examples.
You could use written guide, or video-recorded guide. Any suitable for you.

Given this as the stock image: All you need is make the image looks like the example (1 version for skin, 1 version for color tone, or you could combine skin and tone retouch into 1 version, if possible).
Stock: http://d.qb.io/files/7k9R204P6m8W3x5y1H44/IMG_5283.jpg

Thank you.

• Color tone and skin retouch as example.

```html
<!DOCTYPE html>
<html lang="en">
<head>
<meta charset="utf-8">
<title>Spot reduction guide</title>
<link href="https://fonts.googleapis.com/css2?family=Montserrat:wght@300;400;600&family=Open+Sans:wght@400;600&display=swap" rel="stylesheet">
<style>
:root{
  --paper:#ffffff;
  --ink:#1c1c1c;
  --ui-dark:#3a3a3a;
  --ui-mid:#535353;
  --ui-light:#6a6a6a;
  --ui-line:#2a2a2a;
  --ui-text:#e6e6e6;
  --menu-bg:#e9e9e9;
  --menu-text:#111;
  --flyout:#5c5c5c;
  --tip:#f5f2c8;
  --photo-a:#b9b08a;
  --photo-b:#d6cfae;
  --photo-c:#8c7a5e;
  --wood:#2d2d2d;
}
*{box-sizing:border-box;margin:0;padding:0}
html,body{width:1200px;height:849px;overflow:hidden;background:var(--paper)}
body{position:relative;font-family:"Montserrat",sans-serif;color:var(--ink)}

.heading{position:absolute;left:50px;top:47px}
.heading__title{font-weight:600;font-size:17px;line-height:21px}
.heading__sub{font-weight:300;font-size:17px;line-height:21px}

.step-text{position:absolute;left:50px;font-weight:300;font-size:13.5px;line-height:20px;white-space:nowrap}
.step-text--select{top:220px}
.step-text--aware{top:546px}

/* tool flyout */
.tool-flyout{position:absolute;left:50px;top:332px;width:219px;height:134px;background:var(--ui-mid);overflow:hidden;font-family:"Open Sans",sans-serif}
.tool-flyout__rail{position:absolute;left:0;top:0;width:38px;height:134px;background:var(--ui-dark);border-right:1px solid var(--ui-line)}
.tool-flyout__icon{position:absolute;left:9px;width:20px;height:16px;border-radius:3px;background:#8a8a8a}
.tool-flyout__list{position:absolute;left:38px;top:0;width:176px;height:108px;padding-top:4px;background:var(--flyout);border:1px solid var(--ui-line)}
.tool-flyout__item{display:flex;align-items:center;height:19px;padding-left:18px;font-size:9.5px;font-weight:600;color:var(--ui-text);position:relative;white-space:nowrap}
.tool-flyout__item i{flex:none;width:14px;height:12px;border-radius:2px;background:#9a9a9a;margin-right:7px}
.tool-flyout__item b{position:absolute;right:8px;font-weight:600}
.tool-flyout__item--active::before{content:"";position:absolute;left:6px;width:4px;height:4px;background:var(--ui-text)}
.tool-flyout__under{position:absolute;left:38px;top:108px;width:176px;height:26px;background:#262626}
.tool-flyout__edge{position:absolute;left:214px;top:0;width:5px;height:134px;background:#e9e2d8}

/* options crop */
.options-crop{position:absolute;left:50px;top:580px;width:281px;height:97px;background:var(--ui-mid);overflow:hidden;font-family:"Open Sans",sans-serif}
.options-crop__menu{height:11px;background:var(--menu-bg);font-size:8px;line-height:11px;color:var(--menu-text);padding-left:5px;white-space:nowrap}
.options-crop__title{height:13px;background:#4a4a4a;font-size:7px;line-height:13px;color:var(--ui-text);text-align:right;padding-right:12px}
.options-crop__bar{height:17px;background:var(--ui-light);font-size:5.5px;line-height:17px;color:var(--ui-text);padding-left:3px;white-space:nowrap}
.options-crop__tab{height:10px;background:var(--ui-dark);font-size:5px;line-height:10px;color:var(--ui-text)}
.options-crop__ruler{height:12px;background:#444;border-bottom:1px solid #222;font-size:5px;color:#ccc;line-height:10px;padding-left:16px;word-spacing:20px}
.options-crop__photo{height:34px;background:linear-gradient(90deg,var(--photo-c),var(--photo-a),var(--photo-b),#9ab07a)}

/* main screen */
.screen{position:absolute;left:420px;top:220px;width:731px;height:457px;background:var(--ui-dark);overflow:hidden;font-family:"Open Sans",sans-serif;color:var(--ui-text)}
.screen__menubar{position:absolute;left:0;top:0;width:731px;height:14px;background:var(--menu-bg);color:var(--menu-text);font-size:7.5px;line-height:14px;padding-left:30px;white-space:nowrap}
.screen__menubar strong{font-weight:600}
.screen__status{position:absolute;right:6px;top:0;font-size:7.5px;line-height:14px;color:var(--menu-text);white-space:nowrap}
.screen__titlebar{position:absolute;top:14px;width:731px;height:11px;background:#4b4b4b;font-size:6.5px;line-height:11px;text-align:center}
.screen__lights{position:absolute;left:5px;top:3px;display:flex;gap:4px}
.screen__lights span{width:5px;height:5px;border-radius:50%;background:#d9534f}
.screen__lights span:nth-child(2){background:#e3b341}
.screen__lights span:nth-child(3){background:#5cb85c}
.screen__options{position:absolute;top:25px;width:731px;height:19px;background:var(--ui-light);font-size:5px;line-height:19px;padding-left:78px;white-space:nowrap;border-bottom:1px solid var(--ui-line)}
.screen__workspace{position:absolute;right:6px;top:30px;width:70px;height:9px;background:#555;font-size:5px;line-height:9px;padding-left:4px}
.screen__tab{position:absolute;top:46px;left:10px;height:9px;padding:0 6px;background:var(--ui-mid);font-size:5px;line-height:9px}
.screen__ruler{position:absolute;top:55px;left:23px;width:697px;height:10px;background:#444;font-size:5px;line-height:10px;color:#ccc;word-spacing:10px;padding-left:18px;white-space:nowrap;overflow:hidden}
.screen__tools{position:absolute;top:65px;left:0;width:23px;height:372px;background:var(--ui-mid);border-right:1px solid var(--ui-line)}
.screen__tool{position:absolute;left:7px;width:9px;height:8px;border-radius:2px;background:#9a9a9a}
.screen__tooltip{position:absolute;left:15px;top:256px;height:9px;padding:0 3px;background:var(--tip);color:#222;font-size:5px;line-height:9px;border:1px solid #999}
.screen__photo{position:absolute;top:65px;left:23px;width:697px;height:362px;background:radial-gradient(circle at 62% 40%,#6a4a35 0 14%,transparent 15%),linear-gradient(100deg,#8f8a63 0%,var(--photo-a) 30%,var(--photo-b) 60%,#c9c4a5 100%)}
.screen__dock{position:absolute;top:65px;left:671px;width:60px;height:291px;background:var(--ui-mid);border-left:1px solid var(--ui-line)}
.screen__panel{display:flex;align-items:center;height:16px;padding-left:5px;font-size:5px;white-space:nowrap}
.screen__panel i{width:8px;height:7px;background:#aaa;border-radius:1px;margin-right:7px}
.screen__gap{height:7px;border-bottom:1px solid var(--ui-line)}
.screen__statusbar{position:absolute;top:427px;left:23px;width:697px;height:10px;background:#444;font-size:5px;line-height:10px;padding-left:60px}
.screen__wood{position:absolute;top:437px;left:0;width:731px;height:20px;background:linear-gradient(180deg,#3a3a3a,var(--wood))}
.sp{display:inline-block;width:6px}
</style>
</head>
<body>

<header class="heading">
  <h1 class="heading__title">1. Spot reduction:</h1>
  <h2 class="heading__sub">Removing Spots</h2>
</header>

<p class="step-text step-text--select">On the left hand sidebar select the<br>“Spot healing tool” (If you can’t see the spot<br>healing tool you may need to click and hold<br>down on the 7th icon down, and select it from<br>the choices below).</p>

<div class="tool-flyout">
  <div class="tool-flyout__rail">
    <span class="tool-flyout__icon" style="top:12px"></span>
    <span class="tool-flyout__icon" style="top:44px;background:#777"></span>
    <span class="tool-flyout__icon" style="top:76px;background:#777"></span>
    <span class="tool-flyout__icon" style="top:106px;background:#777"></span>
  </div>
  <div class="tool-flyout__list">
    <div class="tool-flyout__item tool-flyout__item--active"><i></i>Spot Healing Brush Tool<b>J</b></div>
    <div class="tool-flyout__item"><i></i>Healing Brush Tool<b>J</b></div>
    <div class="tool-flyout__item"><i></i>Patch Tool<b>J</b></div>
    <div class="tool-flyout__item"><i></i>Content-Aware Move Tool<b>J</b></div>
    <div class="tool-flyout__item"><i></i>Red Eye Tool<b>J</b></div>
  </div>
  <div class="tool-flyout__under"></div>
  <div class="tool-flyout__edge"></div>
</div>

<p class="step-text step-text--aware">Make sure that the content aware box is checked</p>

<div class="options-crop">
  <div class="options-crop__menu">Image<span class="sp"></span>Layer<span class="sp"></span>Type<span class="sp"></span>Select<span class="sp"></span>Filter<span class="sp"></span>3D<span class="sp"></span>View<span class="sp"></span>Window<span class="sp"></span>Help</div>
  <div class="options-crop__title">Pixel Studio Pro</div>
  <div class="options-crop__bar">Type:<span class="sp"></span>○ Proximity Match<span class="sp"></span>○ Create Texture<span class="sp"></span>◉ Content-Aware<span class="sp"></span>☐ Sample All Layers</div>
  <div class="options-crop__tab">8/8#) *</div>
  <div class="options-crop__ruler">10 20 30 40 50 60 70 80 90 100</div>
  <div class="options-crop__photo" role="img" aria-label="Blurred outdoor background of the portrait"></div>
</div>

<div class="screen">
  <div class="screen__menubar"><strong>Pixel Studio</strong><span class="sp"></span>File<span class="sp"></span>Edit<span class="sp"></span>Image<span class="sp"></span>Layer<span class="sp"></span>Type<span class="sp"></span>Select<span class="sp"></span>Filter<span class="sp"></span>3D<span class="sp"></span>View<span class="sp"></span>Window<span class="sp"></span>Help</div>
  <div class="screen__status">17<span class="sp"></span>Wed 10:58<span class="sp"></span>Dana Whitlow</div>
  <div class="screen__titlebar">
    <div class="screen__lights"><span></span><span></span><span></span></div>
    Pixel Studio Pro
  </div>
  <div class="screen__options">Mode: Normal<span class="sp"></span><span class="sp"></span>Type:<span class="sp"></span>○ Proximity Match<span class="sp"></span>○ Create Texture<span class="sp"></span>◉ Content-Aware<span class="sp"></span>☐ Sample All Layers</div>
  <div class="screen__workspace">Essentials</div>
  <div class="screen__tab">IMG_5283.jpg @ 25% (RGB/8#)</div>
  <div class="screen__ruler">10 15 20 25 30 35 40 45 50 55 60 65 70 75 80 85 90 95 100 105 110 115 120 125 130 135 140 145 150 155 160</div>
  <div class="screen__tools">
    <span class="screen__tool" style="top:20px"></span>
    <span class="screen__tool" style="top:38px"></span>
    <span class="screen__tool" style="top:56px"></span>
    <span class="screen__tool" style="top:74px"></span>
    <span class="screen__tool" style="top:92px"></span>
    <span class="screen__tool" style="top:110px"></span>
    <span class="screen__tool" style="top:128px;background:#ddd"></span>
    <span class="screen__tool" style="top:146px"></span>
    <span class="screen__tool" style="top:164px"></span>
    <span class="screen__tool" style="top:182px"></span>
    <span class="screen__tool" style="top:200px"></span>
    <span class="screen__tool" style="top:218px"></span>
    <span class="screen__tool" style="top:236px"></span>
    <span class="screen__tool" style="top:254px"></span>
    <span class="screen__tool" style="top:272px"></span>
    <span class="screen__tool" style="top:290px"></span>
    <span class="screen__tool" style="top:308px"></span>
    <span class="screen__tool" style="top:330px;background:#5a1a1a"></span>
  </div>
  <div class="screen__photo" role="img" aria-label="Portrait photo of a young woman holding red roses outdoors"></div>
  <div class="screen__tooltip">Spot Healing Brush Tool (J)</div>
  <div class="screen__dock">
    <div class="screen__gap" style="height:2px"></div>
    <div class="screen__panel"><i></i>History</div>
    <div class="screen__panel"><i></i>Layers</div>
    <div class="screen__panel"><i></i>Channels</div>
    <div class="screen__panel"><i></i>Paths</div>
    <div class="screen__panel"><i></i>Color</div>
    <div class="screen__panel"><i></i>Swatches</div>
    <div class="screen__gap"></div>
    <div class="screen__panel"><i></i>Adjustme...</div>
    <div class="screen__panel"><i></i>Styles</div>
    <div class="screen__gap"></div>
    <div class="screen__panel"><i></i>Properties</div>
    <div class="screen__panel"><i></i>Info</div>
    <div class="screen__gap"></div>
    <div class="screen__panel"><i></i>Brush</div>
    <div class="screen__gap"></div>
    <div class="screen__panel"><i></i>Brush Pre...</div>
    <div class="screen__gap"></div>
    <div class="screen__panel"><i></i>Layer Co...</div>
    <div class="screen__panel"><i></i>Notes</div>
    <div class="screen__gap"></div>
    <div class="screen__panel"><i></i>Tool Pres...</div>
  </div>
  <div class="screen__statusbar">Doc: 51.3M/51.3M</div>
  <div class="screen__wood"></div>
</div>

</body>
</html>
```